Business Card for Professional Photographer

I'm looking for an eye catching modern clean design that compliments my logo/ website fonts & colours.
I specialise in architecture, corporate & commercial photography so I'm marketing to professional clients rather than portrait / wedding clients.

I would prefer to not have a solid black design.

My logo brand guide is as follows :

Main front font. : Reislust
Main font colour : #fff
Slogan front font : Ubuntu Bold
Monogram front font : Venti Medium
Container colour : #fff

I need print ready files in pdf .png & .eps formats.

Included in the files below are some screen grabs as reference to font & colours etc.

```html
<!DOCTYPE html>
<html lang="en">
<head>
<meta charset="utf-8">
<title>Clearframe Studio – Business Card</title>
<link href="https://fonts.googleapis.com/css2?family=Didact+Gothic&family=Mulish:wght@700&display=swap" rel="stylesheet">
<style>
  :root {
    --backdrop: #c6c6c6;
    --card: #ffffff;
    --gold: #b98d4a;
    --gold-light: #d2ae66;
    --ink: #474747;
  }
  * { margin: 0; padding: 0; box-sizing: border-box; }
  html, body {
    width: 1125px; height: 1200px; overflow: hidden;
    background: var(--backdrop);
    font-family: "Didact Gothic", sans-serif;
  }
  .card {
    position: absolute; left: 178px; width: 768px; height: 437px;
    background: var(--card); border-radius: 24px;
  }
  .card--front { top: 140px; }
  .card--back { top: 626px; }

  .brand-name {
    position: absolute;
    font-family: "Didact Gothic", sans-serif; font-weight: 400;
    color: var(--gold); text-transform: uppercase;
    white-space: nowrap; line-height: 1;
  }
  .card--front .brand-name {
    left: 46px; top: 205px; font-size: 21px; letter-spacing: 3.6px;
  }
  .card--back .brand-name {
    left: 0; right: 0; top: 196px; text-align: center;
    font-size: 34px; letter-spacing: 6.5px;
  }

  .divider {
    position: absolute; left: 384px; top: 152px; width: 1.5px; height: 134px;
    background: linear-gradient(var(--gold-light), var(--gold));
  }
  .contact { position: absolute; left: 416px; top: 144px; color: var(--ink); }
  .contact__name {
    font-family: "Mulish", sans-serif; font-weight: 700;
    font-size: 25px; color: var(--gold); line-height: 1;
  }
  .contact__role { font-size: 18px; margin-top: 9px; line-height: 1; }
  .contact__list { list-style: none; margin-top: 14px; }
  .contact__item { font-size: 18.5px; line-height: 28px; white-space: nowrap; }
  .contact__label {
    display: inline-block; width: 21px; font-family: "Mulish", sans-serif;
    font-weight: 700; font-size: 16px; color: var(--gold-light);
  }
  .contact__highlight { color: var(--gold-light); }
</style>
</head>
<body>
  <section class="card card--front" aria-label="Card front">
    <p class="brand-name">Clearframe Studio</p>
    <div class="divider"></div>
    <div class="contact">
      <h1 class="contact__name">Dana Whitlow</h1>
      <p class="contact__role">Development Manager</p>
      <ul class="contact__list">
        <li class="contact__item"><span class="contact__label">P</span>: 0400 555 018</li>
        <li class="contact__item"><span class="contact__label">M</span>: dana@clearframestudio.com.au</li>
        <li class="contact__item"><span class="contact__label">W</span>: www.<span class="contact__highlight">clearframestudio</span>.com.au</li>
      </ul>
    </div>
  </section>

  <section class="card card--back" aria-label="Card back">
    <p class="brand-name">Clearframe Studio</p>
  </section>
</body>
</html>
```